Scientific Web Site for KLORVEST

Professional Scientific / Service orientated web site, motto, new logos attached for viewing.

"We measure so the Business Owner can Manage" their environments.
Site needs to be be mobile friendly.

We provide a service to electronically measure cleanliness of any surface and a value added disinfecting fogging surface.

Reports showing locations, trending, tracking and randomized test plans ongoing audits will be made available..

NOTE: Although image of Corona Virus is current we don't wont it plastered through the web site, their is more than the current virus.

Home Page - Professional Scientific / Service Looking
About
Our Approach
Services
Residential
Commercial
Transportation
Gyms
Educational & Daycare
Real Estate - Open for inspections, End of Lease etc

Contact
Mobile #
Email
Form to leave their details

Links to social media, Facebook, Instagram
Reference Sites: Ranked in preference
www.brelmont.com.au
https://www.tidewellhygiene.co.uk/
https://www.mistrova.com/
https://www.zenplax.com.au/specialist-surface-disinfection/
https://www.artfolder.example/design/48172039
https://www.artfolder.example/design/51904476
https://www.artfolder.example/design/47318865

Target Market(s)

Commercial and professional Services

Font styles to use
Sans Serif

Requirements
Must have
• Wix Website
Clean fresh look with appropriate imaging
Web site is a company advertising that will hold static information and we will market through social media.
Nice to have
• Scientific look and feel
Should not have
• Prominent Corona Virus images or references

```html
<!DOCTYPE html>
<html lang="en">
<head>
<meta charset="utf-8">
<title>KLORVEST — Electronically Measure Cleanliness</title>
<link rel="stylesheet" href="https://fonts.googleapis.com/css2?family=Poppins:ital,wght@0,400;0,500;0,600;0,700;0,800;0,900;1,400&display=swap">
<style>
:root{
  --orange:#f07f1f;
  --orange-deep:#e06a0c;
  --ink:#2a2a2a;
  --muted:#7a7a7a;
  --grey-panel:#4a4a4d;
  --soft:#f5f5f5;
  --footer:#231f20;
  --white:#ffffff;
}
*{margin:0;padding:0;box-sizing:border-box}
html,body{width:1200px;height:4454px;overflow:hidden}
body{font-family:'Poppins',sans-serif;color:var(--ink);background:var(--white);position:relative}
a{text-decoration:none}
section,header,footer{position:absolute;left:0;width:1200px}
.abs{position:absolute}
.center{text-align:center;left:0;width:1200px}
.section-title{font-weight:700;font-size:33px;color:var(--orange);letter-spacing:.3px}
.lead{font-size:12px;line-height:22px;color:var(--muted)}

/* header */
.site-header{top:0;height:123px;background:var(--white)}
.brand{left:126px;top:44px;display:flex;align-items:center;gap:10px}
.brand-mark{width:16px;height:16px;border-radius:50%;background:var(--orange)}
.brand-name{font-weight:600;font-size:22px;letter-spacing:2px;color:var(--ink)}
.main-nav{left:469px;top:61px;display:flex;gap:22px;font-size:13px}
.main-nav a{color:var(--ink)}
.main-nav a.active{color:var(--orange)}
.header-phone{left:956px;top:60px;display:flex;align-items:center;gap:10px;font-weight:700;font-size:13px}

/* hero */
.hero{top:123px;height:546px;background:linear-gradient(100deg,#8a4208 0%,#c9630f 40%,#f08a2a 70%,#e6781a 100%);overflow:hidden}
.hero-art{left:560px;top:0;width:640px;height:546px;background:radial-gradient(circle at 65% 55%,#f6a55a 0%,#d9701a 40%,rgba(200,100,20,0) 70%)}
.hero-title{left:126px;top:94px;font-weight:900;font-size:53px;line-height:63px;color:var(--white);letter-spacing:-.5px}
.hero-text{left:128px;top:311px;width:360px;font-size:16px;line-height:27px;color:var(--white)}
.hero-dots{left:124px;top:424px;display:flex;gap:18px;align-items:center}
.hero-dots span{width:8px;height:8px;border-radius:50%;background:var(--white)}
.hero-dots span.on{width:14px;height:14px;border:2px solid var(--white);background:transparent;position:relative}
.hero-dots span.on::after{content:"";position:absolute;left:2px;top:2px;width:6px;height:6px;border-radius:50%;background:var(--white)}

/* about */
.about{top:669px;height:398px}
.about .section-title{top:103px}
.about .lead{top:172px;left:245px;width:710px}
.btn{display:block;background:var(--orange);color:var(--white);font-size:12px;font-weight:500;text-align:center;border-radius:30px}
.about .btn{left:536px;top:271px;width:130px;height:39px;line-height:39px}

/* approach */
.approach{top:1067px;height:517px}
.approach-panel{left:0;top:0;width:600px;height:517px;background:linear-gradient(180deg,#525256 0%,#424245 60%,#2f2f31 100%)}
.approach-photo{left:600px;top:0;width:600px;height:517px;background:linear-gradient(120deg,#f2a35d 0%,#e57a1f 50%,#c45f0c 100%)}
.approach h2{left:130px;top:154px;font-weight:700;font-size:30px;color:var(--white)}
.approach .body{left:132px;top:215px;width:390px;font-size:12px;line-height:22px;color:var(--white)}
.approach .note{left:134px;top:294px;width:260px;font-size:11.5px;line-height:22px;color:var(--white);font-style:italic}

/* services */
.services{top:1584px;height:1006px}
.services .section-title{top:98px}
.services .lead{top:167px;left:0;width:1200px}
.hub{left:0;top:0;width:1200px;height:1006px}
.svc{width:263px}
.svc h3{font-size:16px;font-weight:600;color:#3a3a3a}
.svc p{margin-top:14px;font-size:12px;line-height:22px;color:var(--muted)}
.svc.left{text-align:right}
.svc-res{left:119px;top:320px}
.svc-tra{left:119px;top:519px}
.svc-com{left:813px;top:320px}
.svc-gym{left:813px;top:519px}
.svc.right h3{padding-left:86px}
.svc.left h3{padding-right:91px}
.manage{left:195px;top:710px;width:808px;height:187px;background:var(--soft);border-radius:94px;text-align:center}
.manage h3{margin-top:60px;font-size:16px;font-weight:600;color:#3a3a3a}
.manage p{margin-top:14px;font-size:12px;line-height:22px;color:var(--muted)}

/* areas */
.areas{top:2590px;height:648px;background:linear-gradient(135deg,#e6781a 0%,#f29138 50%,#e26f10 100%)}
.areas h2{top:82px;font-weight:700;font-size:32px;color:var(--white)}
.area-card{top:192px;width:276px;height:358px;background:var(--white)}
.area-card .photo{width:100%;height:192px}
.area-card h3{margin:38px 0 0 39px;font-size:16px;font-weight:700;color:var(--orange)}
.area-card p{margin:16px 0 0 39px;width:200px;font-size:12px;line-height:22px;color:var(--muted)}

/* contact */
.contact{top:3238px;height:704px}
.contact .section-title{top:116px}
.contact .lead{top:193px}
.field{border:1px solid #d6d6d6;border-radius:30px;font-size:12px;color:var(--muted);padding-left:20px;line-height:40px;height:42px;width:391px}
.field.msg{width:808px;height:97px;border-radius:48px;line-height:97px}
.contact .btn{left:424px;top:528px;width:351px;height:41px;line-height:41px}

/* footer */
.site-footer{top:3942px;height:512px;background:var(--footer);color:var(--white)}
.site-footer h4{font-size:16px;font-weight:600}
.f-item{font-size:12px;line-height:19px;color:#e4e4e4}
.f-link{font-size:12px;color:#e4e4e4;display:flex;align-items:center;gap:14px}
.f-link::before{content:"→";font-size:12px;color:var(--white)}
.f-brand{left:904px;top:167px;display:flex;align-items:center;gap:8px}
.f-brand .brand-name{color:var(--white);font-size:22px}
.social{width:28px;height:28px;border-radius:50%;background:var(--white);top:228px}
.copyright{top:455px;font-size:10px;color:#6c6c6c}
</style>
</head>
<body>

<header class="site-header">
  <div class="abs brand"><span class="brand-mark"></span><span class="brand-name">KLORVEST</span></div>
  <nav class="abs main-nav">
    <a class="active" href="#">Home</a><a href="#">About</a><a href="#">Our Approach</a><a href="#">Our Services</a><a href="#">Contact</a>
  </nav>
  <div class="abs header-phone">
    <svg width="18" height="18" viewBox="0 0 24 24" fill="none" stroke="#2a2a2a" stroke-width="1.8"><path d="M5 3h4l2 5-2.5 1.5a11 11 0 0 0 6 6L16 13l5 2v4a2 2 0 0 1-2 2A17 17 0 0 1 3 5a2 2 0 0 1 2-2z"/></svg>
    123-456-7890
  </div>
</header>

<section class="hero">
  <div class="abs hero-art" role="img" aria-label="Orange-toned microscopic view of a cell and DNA strand"></div>
  <h1 class="abs hero-title">Electronically<br>Measure<br>Cleanliness</h1>
  <p class="abs hero-text">We provide a service to electronically measure cleanliness of any surface and a value added disinfecting fogging surface.</p>
  <div class="abs hero-dots"><span class="on"></span><span></span><span></span></div>
</section>

<section class="about">
  <h2 class="abs center section-title">ABOUT COMPANY</h2>
  <p class="abs lead" style="text-align:center">Sed ut perspiciatis unde omnis iste natus error sit voluptatem accusantium doloremque laudantium.Sed ut perspiciatis unde omnis iste natus error sit voluptatem accusantium doloremque laudantium.Sed ut perspiciatis unde omnis iste natus error sit voluptatem accusantium doloremque ium.doloremque</p>
  <a class="abs btn" href="#">View More</a>
</section>

<section class="approach">
  <div class="abs approach-panel" role="img" aria-label="Dark grey laboratory backdrop with test tubes"></div>
  <div class="abs approach-photo" role="img" aria-label="Orange-toned photo of a scientist using a microscope"></div>
  <h2 class="abs">OUR APPROACH</h2>
  <p class="abs body">Sed ut perspiciatis unde omnis iste natus error sit voluptatem accusantium doloremque laudantium.</p>
  <p class="abs note">Locations, Trending, Tracking and Randomized test plans ongoing audits will be made available..</p>
</section>

<section class="services">
  <h2 class="abs center section-title">OUR SERVICES</h2>
  <p class="abs lead" style="text-align:center">Sed ut perspiciatis unde omnis iste natus error sit voluptatem accusantium doloremque laudantium.Sed ut<br>perspiciatis unde omnis iste natus error sit voluptatem accusantium doloremque laudant</p>

  <svg class="abs hub" viewBox="0 0 1200 1006" aria-hidden="true">
    <circle cx="600" cy="449" r="176" fill="none" stroke="#9a9a9a" stroke-width="1.5" stroke-dasharray="6 7"/>
    <circle cx="600" cy="449" r="148" fill="#f4f4f4" stroke="#f07f1f" stroke-width="4"/>
    <text x="600" y="457" text-anchor="middle" font-family="Poppins, sans-serif" font-weight="600" font-size="26" fill="#2a2a2a" letter-spacing="2">KLORVEST</text>
    <g fill="#f07f1f">
      <circle cx="462" cy="340" r="8"/><circle cx="736" cy="340" r="8"/>
      <circle cx="443" cy="524" r="8"/><circle cx="752" cy="536" r="8"/>
      <circle cx="600" cy="625" r="8"/>
    </g>
    <g fill="#fff" stroke="#f07f1f" stroke-width="2">
      <circle cx="363" cy="316" r="37"/><circle cx="363" cy="516" r="37"/>
      <circle cx="840" cy="316" r="37"/><circle cx="840" cy="516" r="37"/>
      <circle cx="600" cy="691" r="37"/>
    </g>
    <g fill="none" stroke="#f07f1f" stroke-width="2" stroke-linecap="round">
      <path d="M352 336h24M356 330h14M360 330l10-24M366 300l8 6M372 318a8 8 0 0 1 -2 14"/>
      <path d="M352 498c14 12 10 24 0 36M374 498c-14 12-10 24 0 36M356 506h14M356 526h14"/>
      <rect x="824" y="300" width="32" height="24" rx="2"/><path d="M834 332h12M840 324v8"/><circle cx="840" cy="312" r="6"/>
      <rect x="826" y="498" width="28" height="36" rx="2"/><path d="M834 496h12v6h-12zM832 512h16M832 520h16M832 528h10"/>
      <circle cx="596" cy="687" r="14"/><path d="M606 697l10 10"/><circle cx="592" cy="683" r="3"/><circle cx="600" cy="690" r="3"/>
    </g>
  </svg>

  <div class="abs svc left svc-res"><h3>RESIDENTIAL</h3><p>Sed ut perspiciatis unde omnis iste natus error sit voluptatem accusantium dolorem-que laudantium.</p></div>
  <div class="abs svc left svc-tra"><h3>TRANSPORTATION</h3><p>Sed ut perspiciatis unde omnis iste natus error sit voluptatem accusantium dolorem-que laudantium.</p></div>
  <div class="abs svc right svc-com"><h3>COMMERCIAL</h3><p>Sed ut perspiciatis unde omnis iste natus error sit voluptatem accusantium dolorem-que laudantium.</p></div>
  <div class="abs svc right svc-gym"><h3>GYMS</h3><p>Sed ut perspiciatis unde omnis iste natus error sit voluptatem accusantium dolorem-que laudantium.</p></div>

  <div class="abs manage">
    <h3>WE MEASURE SO YOU CAN MANAGE</h3>
    <p>Sed ut perspiciatis unde omnis iste natus error sit voluptatem accusantium doloremque laudantium.Sed ut<br>perspiciatis unde omnis iste natus error sit voluptatem accusantium doloremque laudant</p>
  </div>
</section>

<section class="areas">
  <h2 class="abs center">AREAS WE SERVE</h2>
  <article class="abs area-card" style="left:149px">
    <div class="photo" role="img" aria-label="Hands working on a digital tablet interface" style="background:linear-gradient(135deg,#1d3f7a,#6f9ad6 60%,#c9d9ef)"></div>
    <h3>COMMERCIAL</h3><p>Sed ut perspiciatis unde omnis iste natus error sit</p>
  </article>
  <article class="abs area-card" style="left:469px">
    <div class="photo" role="img" aria-label="Laboratory glassware lit by a warm light" style="background:radial-gradient(circle at 55% 50%,#f6e2b0,#a0826a 45%,#3b3a3e)"></div>
    <h3>RESIDENTIAL</h3><p>Sed ut perspiciatis unde omnis iste natus error sit</p>
  </article>
  <article class="abs area-card" style="left:790px">
    <div class="photo" role="img" aria-label="Scientists examining a sample in a bright lab" style="background:linear-gradient(135deg,#dfe6f2,#9aa7c9 50%,#5a4f8a)"></div>
    <h3>TRANSPORTATION</h3><p>Sed ut perspiciatis unde omnis iste natus error sit</p>
  </article>
</section>

<section class="contact">
  <h2 class="abs center section-title">CONTACT FORM</h2>
  <p class="abs center lead">Sed ut perspiciatis unde omnis iste natus error sit voluptatem accusantium doloremque laudantium.Sed ut<br>perspiciatis unde omnis iste natus error sit voluptatem accusantium doloremque laudant</p>
  <div class="abs field" style="left:195px;top:265px">Name</div>
  <div class="abs field" style="left:612px;top:265px">Email</div>
  <div class="abs field" style="left:195px;top:336px">Phone</div>
  <div class="abs field" style="left:612px;top:336px">Subject</div>
  <div class="abs field msg" style="left:195px;top:405px">Message</div>
  <a class="abs btn" href="#">Submit Now</a>
</section>

<footer class="site-footer">
  <h4 class="abs" style="left:161px;top:82px">Get in Touch</h4>
  <h4 class="abs" style="left:432px;top:80px">Quick Links</h4>
  <h4 class="abs" style="left:641px;top:82px">Our Services</h4>

  <svg class="abs" style="left:162px;top:152px" width="30" height="24" viewBox="0 0 30 24" fill="none" stroke="#9a9a9a" stroke-width="1.5"><rect x="1" y="1" width="28" height="22"/><path d="M1 1l14 12L29 1"/></svg>
  <div class="abs f-item" style="left:225px;top:150px">info@mail.com<br>info@klorvest.com</div>
  <svg class="abs" style="left:165px;top:212px" width="20" height="32" viewBox="0 0 20 32" fill="none" stroke="#9a9a9a" stroke-width="1.5"><rect x="1" y="1" width="18" height="30" rx="2"/><path d="M1 24h18M8 28h4"/></svg>
  <div class="abs f-item" style="left:222px;top:218px">+123 456 7890<br>+123 456 7890</div>
  <svg class="abs" style="left:161px;top:272px" width="30" height="36" viewBox="0 0 30 36" fill="none" stroke="#9a9a9a" stroke-width="1.5"><path d="M15 30s10-10 10-18a10 10 0 0 0-20 0c0 8 10 18 10 18z"/><circle cx="15" cy="12" r="4"/><path d="M3 30l-2 5h28l-2-5"/></svg>
  <div class="abs f-item" style="left:226px;top:292px">123, Main Road, New<br>City, My Country 123456</div>

  <div class="abs" style="left:440px;top:148px">
    <div class="f-link" style="height:29px">About us</div>
    <div class="f-link" style="height:29px">Blog</div>
    <div class="f-link" style="height:29px">Contact us</div>
    <div class="f-link" style="height:29px">Faq</div>
    <div class="f-link" style="height:29px">Insurance</div>
    <div class="f-link" style="height:29px">Contact us</div>
  </div>
  <div class="abs" style="left:638px;top:150px">
    <div class="f-link" style="height:29px">Residential</div>
    <div class="f-link" style="height:29px">Commercial</div>
    <div class="f-link" style="height:29px">Transportation</div>
    <div class="f-link" style="height:29px">Gyms</div>
    <div class="f-link" style="height:29px">Educational &amp; Daycare</div>
    <div class="f-link" style="height:29px">Real Estate</div>
  </div>

  <div class="abs f-brand"><span class="brand-mark"></span><span class="brand-name">KLORVEST</span></div>
  <a class="abs social" style="left:952px" href="#" aria-label="Social profile"></a>
  <a class="abs social" style="left:989px" href="#" aria-label="Photo sharing profile"></a>

  <p class="abs center copyright">©2020 KLORVEST. All rights reserved.</p>
</footer>

</body>
</html>
```